Business Cards for a law firm

Business cards for our law firm. Use our silhoette logo and OAK PARTNERS - check our website (www.oakpartners.example)

Contact Information for Business Card

our silhouette logo, OAK PARTNERS, 800-555-0147, Dorian Pemberton, dorian@oakpartners.example

Requirements
Must have
• our silhouette logo, OAK PARTNERS, 800-555-0147, Dorian Pemberton, dorian@oakpartners.example

```html
<!DOCTYPE html>
<html lang="en">
<head>
<meta charset="utf-8">
<title>Oak Partners — Business Cards</title>
<link href="https://fonts.googleapis.com/css2?family=Marcellus+SC&display=swap" rel="stylesheet">
<style>
  :root {
    --navy: #213069;
    --navy-soft: rgba(33, 48, 105, 0);
    --paper: #ffffff;
    --backdrop: #e1e6e8;
    --ink-light: #ffffff;
  }
  * { box-sizing: border-box; margin: 0; padding: 0; }
  html, body {
    width: 1200px; height: 960px; overflow: hidden;
    background: var(--backdrop);
    font-family: "Marcellus SC", "Times New Roman", serif;
    color: var(--navy);
  }
  .card {
    position: absolute; left: 249px; width: 701px; height: 400px;
    background: var(--paper);
  }
  .card--front { top: 60px; }
  .card--back { top: 500px; }

  .brand-mark {
    position: absolute; background: var(--navy);
  }
  .card--front .brand-mark { left: 124px; top: 152px; width: 82px; height: 82px; }
  .card--back .brand-mark { left: 184px; top: 56px; width: 38px; height: 38px; }

  .brand-name { position: absolute; color: var(--navy); line-height: 1; white-space: nowrap; }
  .card--front .brand-name {
    left: 232px; top: 134px; font-size: 56px; letter-spacing: 3px; line-height: 48px;
  }
  .card--back .brand-name {
    left: 232px; top: 58px; font-size: 33px; letter-spacing: 2px;
  }

  .band {
    position: absolute; left: 7px; right: 7px;
    display: flex; align-items: center; justify-content: center;
    background: linear-gradient(90deg, var(--navy-soft) 0%, rgba(33,48,105,0.35) 20%, rgba(33,48,105,0.75) 42%, var(--navy) 50%, rgba(33,48,105,0.75) 58%, rgba(33,48,105,0.35) 80%, var(--navy-soft) 100%);
    color: var(--ink-light);
  }
  .band--web { top: 347px; height: 27px; font-size: 17px; letter-spacing: 1.5px; }
  .band--name { top: 171px; height: 59px; font-size: 30px; letter-spacing: 2px; font-weight: 700; -webkit-text-stroke: 0.8px var(--ink-light); }

  .contact-icons {
    position: absolute; top: 253px; left: 0; right: 0;
    display: flex; justify-content: center; gap: 8px;
  }
  .contact-icons svg { width: 30px; height: 30px; }

  .contact-list {
    position: absolute; top: 292px; left: 0; right: 0;
    text-align: center; list-style: none; color: var(--navy);
  }
  .contact-list li { line-height: 1; }
  .contact-list .phone { font-size: 23px; letter-spacing: 1px; margin-bottom: 9px; }
  .contact-list .web, .contact-list .email { font-size: 18px; letter-spacing: 1px; margin-bottom: 6px; }
</style>
</head>
<body>
  <section class="card card--front">
    <div class="brand-mark"></div>
    <h1 class="brand-name">OAK<br>PARTNERS</h1>
    <div class="band band--web">WWW.OAKPARTNERS.EXAMPLE</div>
  </section>

  <section class="card card--back">
    <div class="brand-mark"></div>
    <h2 class="brand-name">OAK PARTNERS</h2>
    <div class="band band--name">DORIAN PEMBERTON</div>

    <div class="contact-icons">
      <svg viewBox="0 0 30 30" aria-label="Phone">
        <rect x="6" y="6" width="18" height="18" rx="3" transform="rotate(45 15 15)" fill="var(--navy)"/>
        <path d="M11.5 10.5c1-.8 1.6-.6 2 .2l.8 1.5c.3.6.1 1-.4 1.4l-.6.4c.5 1.3 1.4 2.3 2.7 2.9l.5-.6c.4-.5.9-.6 1.4-.3l1.5.9c.7.4.8 1 .1 1.9-1.2 1.4-3.6.6-5.7-1.5s-3.3-5-2.3-6.8z" fill="var(--ink-light)"/>
      </svg>
      <svg viewBox="0 0 30 30" aria-label="Email">
        <rect x="6" y="6" width="18" height="18" rx="3" transform="rotate(45 15 15)" fill="var(--navy)"/>
        <rect x="9.5" y="11" width="11" height="8" fill="none" stroke="var(--ink-light)" stroke-width="1.2"/>
        <path d="M9.5 11l5.5 4.5 5.5-4.5" fill="none" stroke="var(--ink-light)" stroke-width="1.2"/>
      </svg>
      <svg viewBox="0 0 30 30" aria-label="Website">
        <rect x="6" y="6" width="18" height="18" rx="3" transform="rotate(45 15 15)" fill="var(--navy)"/>
        <circle cx="15" cy="15" r="5.5" fill="none" stroke="var(--ink-light)" stroke-width="1.2"/>
        <ellipse cx="15" cy="15" rx="2.3" ry="5.5" fill="none" stroke="var(--ink-light)" stroke-width="1"/>
        <path d="M9.5 15h11" stroke="var(--ink-light)" stroke-width="1"/>
      </svg>
    </div>

    <ul class="contact-list">
      <li class="phone">800-555-0147</li>
      <li class="web">WWW.OAKPARTNERS.EXAMPLE</li>
      <li class="email">DORIAN@OAKPARTNERS.EXAMPLE</li>
    </ul>
  </section>
</body>
</html>
```